Application for baby milk and water counter

We are building baby food app. Need to design main screen for tha app first so we can go forward to other secondary screens of the app

Food dashboard screen
Food dashboard screen is main page for view/edit food data

General vision
I see the app in pastel colors with some illustrations to make the app more in positive. You can influence from game Glimmer Tides. I see with smooth colors and gradients like in a game. Also need to have animations/transitions for each action. Each click should create smooth transition to new state. My idea is to build one dashboard screen for food which we can reuse it for other screens. So a lot of thinking should go into design stage to app appealing.

Food Dashboard
Current screen should show all the data about food intake of the baby. So here user should see

Milk How much food baby had in ml/oz. So there should be some kind of illustrated bottle or glass or smth that shows it is filled with that amount.

Add/Remove controls for food. Should be some kind of custom control for inputing amount to remove/add. I see it as a slider on the side of the bottle. User slides up or down and amount is added/removed.

Notification. So user should be aware how many hours/minutes left for next food intake. This is optional field, so consider it could be disabled. So no empty space should be on a screen. There should be human readable text. Something like. 1:30 minutes left for next intake. Maybe could be some custom made icons to illustrate that it is next food intake.

Burped: User should have ability to how much baby burped. This amount is integer value. So it could be “Baby burped 2 times today”. So again here I see some custom made/icon to illustrate how many times baby burped and amount next to it. I see changing the value just by tapping, but I don’t know how to edit if user tapped accidentally more than it should be. So TBD here.

Date and time: Dashboard should show for which date it is viewing/editing data. Should be able to change it, so user can add/edit data for yesterday. Don’t want to see here calendar on a screen so need to come up with nice design decision.

Water: User should have ability to view/edit water intake of the baby, but water is secondary information so it should be smaller than milk, or come up with some other idea how to show the water. I see to have same controls for water like for milk. Water intake is optional it can be disabled by the user.

Target Market(s)

For just became mothers

Font styles to use
Sans Serif

Colors
0094D4
00A9DD
6FCCEA
C7EBF8
E9F6FB
FFC000
F8CF3A
FAE287
FDF2CF
FEFAEE
E54698
E96AAD
F1A4CE
F9D9EA
FCEFF6

Requirements
Must have
• Ilustrations or playfull icons for show information

```html
<!DOCTYPE html>
<html lang="en">
<head>
<meta charset="utf-8">
<title>Baby Food Dashboard</title>
<link href="https://fonts.googleapis.com/css2?family=Lato:wght@400;700;900&display=swap" rel="stylesheet">
<style>
:root{
  --blue-dark:#0094D4;
  --blue:#00A9DD;
  --blue-soft:#C7EBF8;
  --blue-pale:#E9F6FB;
  --pink:#E54698;
  --pink-mid:#E96AAD;
  --pink-soft:#F9D9EA;
  --lavender:#E4E3F1;
  --ink:#2b2b2b;
  --grey:#666;
  --line:#d2d2d2;
  --white:#fff;
}
*{margin:0;padding:0;box-sizing:border-box}
html,body{width:675px;height:1200px;overflow:hidden}
body{font-family:"Lato",sans-serif;color:var(--ink);background:var(--white)}
.screen{position:relative;width:675px;height:1200px;overflow:hidden;background:var(--white)}
.sky{position:absolute;left:0;top:0;width:675px;height:420px}
.hero-art{position:absolute;left:250px;top:0;width:260px;height:245px;border-radius:50% 50% 40% 40%;
  background:radial-gradient(circle at 45% 45%,#f6d2bd 0%,#c9c3e0 70%,rgba(201,195,224,0) 100%)}
.field{position:absolute;top:270px;width:156px;height:54px;border-bottom:2px dashed #9a9a9a;
  display:flex;align-items:center;justify-content:space-between;font-size:27px;color:#777}
.field-date{left:90px}
.field-time{left:430px}
.field svg{width:30px;height:30px}
.card{position:absolute;left:90px;top:356px;width:495px;height:594px;background:var(--white);
  border-radius:8px;box-shadow:0 3px 18px rgba(0,0,0,.12)}
.section{position:absolute;left:0;width:495px;height:200px}
.section + .section{border-top:2px solid var(--line)}
.section-milk{top:0}
.section-water{top:202px}
.section-burp{top:400px;height:194px}
.section-title{position:absolute;left:54px;top:38px;font-size:25px;font-weight:700;color:var(--blue-dark)}
.icon-art{position:absolute;border-radius:10px}
.icon-milk{left:54px;top:90px;width:45px;height:85px;background:linear-gradient(#7fd3c8,#b9ebe4)}
.icon-water{left:54px;top:81px;width:45px;height:90px;background:linear-gradient(#9ad3ef,#d9eefa)}
.icon-burp{left:50px;top:83px;width:67px;height:88px;border-radius:50%;background:linear-gradient(#f4c98f,#e2e6ee)}
.stat{position:absolute;top:96px}
.stat-total{left:157px}
.stat-intake{left:290px}
.stat-label{font-size:29px;font-weight:900;line-height:1}
.stat-value{margin-top:16px;font-size:20px;color:var(--grey);display:flex;align-items:center;gap:14px}
.stepper{display:flex;gap:12px}
.stepper svg{width:17px;height:17px}
.notice{position:absolute;left:95px;top:1001px;width:486px;height:65px;border-radius:4px;background:var(--pink);
  color:var(--white);font-size:20px;font-weight:700;display:flex;align-items:center;justify-content:center}
.corner-art{position:absolute;left:0;top:885px;width:215px;height:315px;
  background:linear-gradient(160deg,#eef4fa 0%,#f7dccd 100%);border-radius:40% 40% 0 0;opacity:.85}
</style>
</head>
<body>
<main class="screen">
  <svg class="sky" viewBox="0 0 675 420" aria-hidden="true">
    <rect width="675" height="420" fill="#fff"/>
    <path d="M0 0H675V370C560 320 470 330 340 390 210 330 110 330 0 380Z" fill="var(--lavender)"/>
    <path d="M0 380C110 330 210 330 340 390 250 350 120 340 0 420Z" fill="#f7dbe6"/>
    <path d="M340 390C470 330 560 320 675 370V420C580 340 450 345 340 390Z" fill="#d6ecf7"/>
  </svg>
  <div class="hero-art" role="img" aria-label="Illustration of a playful baby with a milk bottle"></div>

  <div class="field field-date">Date
    <svg viewBox="0 0 24 24" aria-hidden="true"><rect x="3" y="5" width="18" height="16" rx="2" fill="#6f6f6f"/><rect x="5" y="10" width="14" height="9" fill="#fff"/><g fill="#6f6f6f"><rect x="6" y="11" width="3" height="2"/><rect x="10.5" y="11" width="3" height="2"/><rect x="15" y="11" width="3" height="2"/><rect x="6" y="15" width="3" height="2"/><rect x="10.5" y="15" width="3" height="2"/><rect x="15" y="15" width="3" height="2"/><rect x="7" y="3" width="2" height="4"/><rect x="15" y="3" width="2" height="4"/></g></svg>
  </div>
  <div class="field field-time">Time
    <svg viewBox="0 0 24 24" aria-hidden="true"><circle cx="12" cy="12" r="10" fill="#6f6f6f"/><path d="M12 6v6l4 3" stroke="#fff" stroke-width="2" fill="none" stroke-linecap="round"/></svg>
  </div>

  <section class="card">
    <div class="section section-milk">
      <h2 class="section-title">Milk</h2>
      <div class="icon-art icon-milk" role="img" aria-label="Milk bottle illustration"></div>
      <div class="stat stat-total"><div class="stat-label">Total</div><div class="stat-value">200 ml</div></div>
      <div class="stat stat-intake"><div class="stat-label">In take</div>
        <div class="stat-value">80 ml
          <span class="stepper">
            <svg viewBox="0 0 16 16" aria-label="Add"><circle cx="8" cy="8" r="8" fill="#7b5fd6"/><path d="M4 8h8M8 4v8" stroke="#fff" stroke-width="2"/></svg>
            <svg viewBox="0 0 16 16" aria-label="Remove"><circle cx="8" cy="8" r="8" fill="var(--pink-mid)"/><path d="M4 8h8" stroke="#fff" stroke-width="2"/></svg>
          </span></div></div>
    </div>
    <div class="section section-water">
      <h2 class="section-title">Water</h2>
      <div class="icon-art icon-water" role="img" aria-label="Water bottle illustration"></div>
      <div class="stat stat-total"><div class="stat-label">Total</div><div class="stat-value">200 ml</div></div>
      <div class="stat stat-intake"><div class="stat-label">In take</div>
        <div class="stat-value">80 ml
          <span class="stepper">
            <svg viewBox="0 0 16 16" aria-label="Add"><circle cx="8" cy="8" r="8" fill="#7b5fd6"/><path d="M4 8h8M8 4v8" stroke="#fff" stroke-width="2"/></svg>
            <svg viewBox="0 0 16 16" aria-label="Remove"><circle cx="8" cy="8" r="8" fill="var(--pink-mid)"/><path d="M4 8h8" stroke="#fff" stroke-width="2"/></svg>
          </span></div></div>
    </div>
    <div class="section section-burp">
      <h2 class="section-title">Burped</h2>
      <div class="icon-art icon-burp" role="img" aria-label="Sitting baby illustration"></div>
      <div class="stat stat-total"><div class="stat-label">Total</div><div class="stat-value">2 Times</div></div>
    </div>
  </section>

  <div class="corner-art" role="img" aria-label="Illustration of a baby beside a large milk bottle"></div>
  <div class="notice">2 Hours 40 Minutes left for next intake</div>
</main>
</body>
</html>
```